Marlow Estate Fixers (Handyman / Home Improvement Company)

Looking for a double sided professional looking business card with Logo attached to be highlighted on one side and throwing in an image of a handyman as an option would be nice to see as well. We are a company focused on providing quality Handyman and Home improvement services in a timely manner that is done right the first time with integrity

Industry/Entity Type

Handyman / Home Improvement

Contact Information for Business Card

(LOGO, Name, Mobile and office phone numbers, email) on front side of card, (the words "The SOLUTION to all of your Handyman and Home Improvement needs" followed by "Family Owned and Operated" at the very bottom) on the back.

Colors
EB3D1F
EC4F4E
F09395
F8D3D4
FCEDEE

Requirements
Must have
• Red, Gray, Black Color scheme
Should not have
• No Yellow or Blue colors

```html
<!DOCTYPE html>
<html lang="en">
<head>
<meta charset="utf-8">
<title>Marlow Estate Fixers – Business Card</title>
<link href="https://fonts.googleapis.com/css2?family=Poppins:wght@300;400;500;600;700&display=swap" rel="stylesheet">
<style>
  :root {
    --stage: #232323;
    --card: #222125;
    --card-deep: #1b1a1d;
    --pattern-a: #2a292d;
    --pattern-b: #1e1d21;
    --red: #eb3d1f;
    --red-soft: #ec4f4e;
    --emboss: #2f2e33;
    --emboss-light: #3a393e;
    --white: #ffffff;
  }
  * { margin: 0; padding: 0; box-sizing: border-box; }
  html, body {
    width: 1200px; height: 800px; overflow: hidden;
    background: var(--stage);
    font-family: "Poppins", sans-serif;
    color: var(--white);
  }
  .stage {
    width: 1200px; height: 800px;
    display: flex; align-items: center; justify-content: center; gap: 40px;
  }
  .card {
    position: relative;
    width: 540px; height: 310px;
    background: var(--card);
    border-bottom: 6px solid var(--red);
    overflow: hidden;
    box-shadow: 0 18px 40px rgba(0,0,0,.55);
  }

  /* Tagline side */
  .card--tagline .pattern-fill {
    position: absolute; inset: 0;
    background: radial-gradient(circle at 50% 45%, var(--pattern-a), var(--pattern-b) 75%);
  }
  .card--tagline .brand {
    position: absolute; left: 0; right: 0; top: 96px;
    display: flex; align-items: center; justify-content: center; gap: 12px;
  }
  .brand-mark {
    width: 22px; height: 22px; background: var(--red);
  }
  .brand-name {
    font-size: 30px; font-weight: 700; letter-spacing: .5px;
    color: var(--white); text-transform: uppercase;
  }
  .tagline-block {
    position: absolute; left: 0; right: 0; bottom: 40px; text-align: center;
  }
  .tagline-family {
    font-size: 15px; font-weight: 400; color: var(--red-soft); letter-spacing: .3px;
  }
  .tagline-main {
    margin-top: 8px; font-size: 13px; font-weight: 400; color: var(--white);
  }

  /* Contact side */
  .card--contact .accent-bar {
    position: absolute; left: 0; top: 34px; width: 8px; height: 62px; background: var(--red);
  }
  .person { position: absolute; left: 34px; top: 30px; }
  .person-name { font-size: 30px; line-height: 1.1; color: var(--red-soft); }
  .person-name .first { font-weight: 700; }
  .person-name .last { font-weight: 300; }
  .person-role { font-size: 14px; font-weight: 600; margin-top: 2px; letter-spacing: .3px; }

  .address {
    position: absolute; left: 72px; top: 150px;
    font-size: 13px; line-height: 1.45; font-weight: 400;
  }
  .contacts {
    position: absolute; left: 72px; top: 200px; list-style: none;
    font-size: 13px; line-height: 1.6;
  }
  .contacts li { display: flex; align-items: center; gap: 8px; }
  .contacts svg { width: 13px; height: 13px; flex: none; }
  .contacts .hl { color: var(--red-soft); }

  .card--contact .brand {
    position: absolute; right: 26px; top: 110px;
    display: flex; align-items: center; gap: 10px;
  }
  .card--contact .brand-mark { background: var(--emboss-light); width: 18px; height: 18px; }
  .card--contact .brand-name {
    font-size: 22px; color: var(--emboss-light);
  }
</style>
</head>
<body>
<main class="stage">

  <section class="card card--tagline" aria-label="Card back">
    <div class="pattern-fill" role="img" aria-label="Faint repeating embossed pattern of the company emblem"></div>
    <div class="brand">
      <span class="brand-mark"></span>
      <span class="brand-name">Marlow Estate Fixers</span>
    </div>
    <div class="tagline-block">
      <p class="tagline-family">Family Owned and Operated</p>
      <p class="tagline-main">Your SOLUTION to all of your Handyman and Home Improvement needs</p>
    </div>
  </section>

  <section class="card card--contact" aria-label="Card front">
    <span class="accent-bar"></span>
    <div class="person">
      <h1 class="person-name"><span class="first">Rena</span> <span class="last">Calloway</span></h1>
      <p class="person-role">Founder &amp; CEO</p>
    </div>

    <address class="address" style="font-style:normal">
      418 Linden Row, Suite 12<br>
      Brookfield, TX 76021
    </address>

    <ul class="contacts">
      <li>
        <svg viewBox="0 0 14 14" fill="none" stroke="var(--red)" stroke-width="1.4"><rect x="3.5" y="1" width="7" height="12" rx="1.2"/><line x1="6" y1="11" x2="8" y2="11"/></svg>
        (555) 214-3068
      </li>
      <li>
        <svg viewBox="0 0 14 14" fill="var(--red)"><path d="M3 1.5l2.2 0 1 3-1.4 1.2a7 7 0 0 0 3.5 3.5L9.5 7.8l3 1V11a1.5 1.5 0 0 1-1.6 1.5A10.5 10.5 0 0 1 1.5 3.1 1.5 1.5 0 0 1 3 1.5z"/></svg>
        (555) 214-7700
      </li>
      <li>
        <svg viewBox="0 0 14 14" fill="none" stroke="var(--red)" stroke-width="1.3"><circle cx="7" cy="7" r="5.8"/><ellipse cx="7" cy="7" rx="2.5" ry="5.8"/><line x1="1.2" y1="7" x2="12.8" y2="7"/></svg>
        <span>www.<span class="hl">marlowfixers</span>.com</span>
      </li>
      <li>
        <svg viewBox="0 0 14 14" fill="none" stroke="var(--red)" stroke-width="1.3"><rect x="1" y="3" width="12" height="8.5" rx="1"/><path d="M1 3.5l6 4.5 6-4.5"/></svg>
        <span>info@<span class="hl">marlowfixers</span>.com</span>
      </li>
    </ul>

    <div class="brand">
      <span class="brand-mark"></span>
      <span class="brand-name">Marlow Estate Fixers</span>
    </div>
  </section>

</main>
</body>
</html>
```